Flyer-Design für trommel-welt
Zielgruppe
Website und Onlineshop rund um die irische Rahmentrommel 'bodhrán'. Wir bieten Informationen, Kaufberatung und einen Onlineshop. Wir sind auf Qualitätsinstrumente spezialisiert und verkaufen keine billigen Instrumente aus Fernost.
Aufgabenstellung
Wir haben die Website komplett neu gestaltet und brauchen nun einen neuen Flyer im Stil der Website. Die Adresse ist www.trommel-welt.de Es müsste also auf den Bildern und ungefähr dem Design der Website beruhen. Die Bilder kann ich dann natürlich zur Verfügung stellen. Beim Format würde ich gerne etwas kleineres längliches nehmen und auf 300er Recycling Papier drucken. Hatte vorher DIN lang, aber ich habe hier Flyer in 14*6,5 cm gesehen, die fand ich auch schön.
Die Seite ist deutsch und englisch, daher sollte der Flyer eine Seite deutsch, eine Seite englisch haben.

```html
<!DOCTYPE html>
<html lang="de">
<head>
<meta charset="utf-8">
<title>trommel-welt Flyer</title>
<link rel="stylesheet" href="https://fonts.googleapis.com/css2?family=Fira+Sans:wght@300;400;500;600&display=swap">
<style>
  :root {
    --brand-red: #a12d1a;
    --ink: #111111;
    --muted: #5a5a5a;
    --paper: #ffffff;
    --frame: #9a9a9a;
    --square: #2a2a2a;
  }
  * { margin: 0; padding: 0; box-sizing: border-box; }
  html, body { width: 1200px; height: 2584px; overflow: hidden; background: var(--paper); }
  .flyer {
    position: relative; width: 1200px; height: 2584px;
    background: var(--paper); border: 2px solid var(--frame); overflow: hidden;
    font-family: "Fira Sans", sans-serif; color: var(--ink);
  }
  .hero { position: absolute; left: 0; top: 0; width: 1200px; height: 700px; }

  .brand { position: absolute; left: 130px; top: 782px; display: flex; align-items: center; }
  .brand-square { width: 130px; height: 130px; background: var(--square); border-radius: 14px; margin-right: 30px; flex: none; }
  .brand-name {
    font-weight: 500; color: var(--brand-red);
    font-size: 104px; line-height: 1; letter-spacing: -1px;
  }
  .brand-tagline {
    font-size: 24px; font-weight: 500; letter-spacing: 3px; color: var(--ink);
    margin-top: 12px; white-space: nowrap;
  }

  .intro {
    position: absolute; left: 131px; top: 1008px; width: 980px;
    font-size: 48px; font-weight: 500; line-height: 62.5px;
  }
  .section-head { position: absolute; left: 125px; display: flex; align-items: center; }
  .section-head svg { width: 96px; height: 96px; margin-right: 42px; }
  .section-head h2 { font-size: 58px; font-weight: 500; }
  .section-head.info { top: 1330px; }
  .section-head.shop { top: 1784px; }
  .section-head.shop svg { width: 86px; height: 86px; margin-right: 46px; }
  .checklist { position: absolute; left: 125px; list-style: none; font-size: 48px; font-weight: 300; color: var(--muted); line-height: 62.5px; }
  .checklist li { position: relative; padding-left: 82px; }
  .checklist li svg { position: absolute; left: 4px; top: 16px; width: 42px; height: 34px; }
  .checklist.info { top: 1472px; }
  .checklist.shop { top: 1924px; }
  .checklist.shop li { padding-left: 78px; }
  .web {
    position: absolute; right: 130px; top: 2257px;
    font-size: 50px; font-weight: 500; color: var(--ink);
  }

  .footer-band { position: absolute; left: 0; top: 2380px; width: 1200px; height: 204px; background: var(--brand-red); color: var(--paper); }
  .partner { position: absolute; left: 125px; top: 60px; text-align: center; font-weight: 500; }
  .partner-name { font-size: 40px; letter-spacing: 1px; line-height: 1.1; }
  .partner-tier { font-size: 28px; letter-spacing: 1px; }
  .label-name { position: absolute; right: 130px; top: 48px; font-weight: 500; font-size: 72px; }
</style>
</head>
<body>
<div class="flyer">
  <svg class="hero" viewBox="0 0 1200 700">
    <defs>
      <linearGradient id="drumTones" x1="0" y1="0" x2="1" y2="0">
        <stop offset="0" stop-color="#b8421f"/>
        <stop offset="0.3" stop-color="#c8532a"/>
        <stop offset="0.45" stop-color="#1b2c3a"/>
        <stop offset="0.6" stop-color="#2f6f8e"/>
        <stop offset="0.75" stop-color="#d7c29a"/>
        <stop offset="1" stop-color="#9c5a32"/>
      </linearGradient>
    </defs>
    <path role="img" aria-label="Foto: Nahaufnahme mehrerer Bodhrán-Rahmentrommeln mit Holzrahmen" d="M0 0 H1200 V470 C900 600 400 660 0 420 Z" fill="url(#drumTones)"/>
    <path d="M0 420 C400 660 900 600 1200 470 V490 C900 680 380 720 0 560 Z" fill="var(--brand-red)"/>
  </svg>

  <div class="brand">
    <div class="brand-square"></div>
    <div>
      <div class="brand-name">trommel-welt</div>
      <div class="brand-tagline">DIE WELT DER IRISCHEN RAHMENTROMMEL</div>
    </div>
  </div>

  <p class="intro">Wir bieten individuelle Beratung,<br>die auf einer 30-jährigen Erfahrung<br>im professionellem Bodhránspiel<br>und Unterricht aufbaut.</p>

  <div class="section-head info">
    <svg viewBox="0 0 60 60" fill="none" stroke="var(--brand-red)" stroke-width="3">
      <path d="M4 18 L30 5 L56 18 Z"/><rect x="4" y="18" width="52" height="5"/>
      <path d="M10 23 V48 M18 23 V48 M26 23 V48 M34 23 V48 M42 23 V48 M50 23 V48"/>
      <rect x="4" y="48" width="52" height="4"/><rect x="1" y="52" width="58" height="5"/>
    </svg>
    <h2>Die irische Rahmentrommel</h2>
  </div>
  <ul class="checklist info">
    <li><svg viewBox="0 0 42 34"><path d="M3 17 L15 29 L39 4" fill="none" stroke="var(--brand-red)" stroke-width="4"/></svg>Alles über die Bodhrán</li>
    <li><svg viewBox="0 0 42 34"><path d="M3 17 L15 29 L39 4" fill="none" stroke="var(--brand-red)" stroke-width="4"/></svg>Ratgeber zum Bodhránkauf</li>
    <li><svg viewBox="0 0 42 34"><path d="M3 17 L15 29 L39 4" fill="none" stroke="var(--brand-red)" stroke-width="4"/></svg>Infos über Tipper, Geschichte<br>und Konstruktion</li>
  </ul>

  <div class="section-head shop">
    <svg viewBox="0 0 60 60" fill="none" stroke="var(--brand-red)" stroke-width="3">
      <rect x="3" y="3" width="54" height="54"/>
      <path d="M3 14 H57 M3 24 H57 M12 14 V24 M21 14 V24 M30 14 V24 M39 14 V24 M48 14 V24"/>
      <rect x="9" y="32" width="20" height="14"/><path d="M36 57 V32 H50 V57"/>
    </svg>
    <h2>Online Shop</h2>
  </div>
  <ul class="checklist shop">
    <li><svg viewBox="0 0 42 34"><path d="M3 17 L15 29 L39 4" fill="none" stroke="var(--brand-red)" stroke-width="4"/></svg>Handgefertigte Bodhráns und Tipper</li>
    <li><svg viewBox="0 0 42 34"><path d="M3 17 L15 29 L39 4" fill="none" stroke="var(--brand-red)" stroke-width="4"/></svg>TrommelKonfigurator zum<br>Konfigurieren individueller Bodhráns</li>
    <li><svg viewBox="0 0 42 34"><path d="M3 17 L15 29 L39 4" fill="none" stroke="var(--brand-red)" stroke-width="4"/></svg>Taschen, Zubehör, Lernmaterial<br>und CDs</li>
  </ul>

  <div class="web">www.trommel-welt.de</div>

  <footer class="footer-band">
    <div class="partner">
      <div class="partner-name">KELLERWALD DRUMS</div>
      <div class="partner-tier">PREMIUM PARTNER</div>
    </div>
    <div class="label-name">lorant</div>
  </footer>
</div>
</body>
</html>
```